Exciting product design for natural pet treats

We need a design for our stand up doy style pouch that blends well with our current logo and also bold enough to stand out from the crowd.

We have a range of natural, Australian made pet treats and need a generic bag that allows for a sticker to be placed on the bag to idenfity the name, while also allowing a space for another sticker on the back for ingredients.
___
Information for the front is: logo, Australian made and owned, Pet Food Only (this is a small font and should not be hero text), 100% Natural, Visit our web site for more amazing products for your pets, Space for sticker 100 - 150mm x 30mm.
___
Information for the back is: Tailwag Depot is proudly Australian owned and operated. We source all our Tailwag Depot treats from reputable suppliers around Australia.

Our Tailwag Depot treats can be purchased through our online store, where you will find a growing range of other brands and products for your dogs, cats, birds, fish, rabbits, guinea pigs, horses, cows, sheep, chickens and more.

For further information, please visit our web site www.tailwagdepot.com.au or email us directly info@tailwagdepot.com.au.
____
The design will be used on three different bag sizes, so our printer can reduce the design from the largest size, but please keep in mind the sizes are 280mm x 380mm, 190mm x 275mm & 160mm x 230mm.

Target Market(s)

Mostly female, 25 to 65 years of age. Pet Lovers, particuarly focussing on dogs.

Industry/Entity Type

pet industry

Requirements
Must have
• Space for sticker on front for the product name 100mm x 30mm. Also a
Nice to have
• Space for a window.
Should not have
• comical pet images. Does not need an image of a pet. Does not need an image of the food.

```html
<!DOCTYPE html>
<html lang="en">
<head>
<meta charset="utf-8">
<title>Tailwag Depot – Treat Pouch Front and Back</title>
<link rel="stylesheet" href="https://fonts.googleapis.com/css2?family=Alegreya+Sans:wght@400;700&family=Fjalla+One&family=Oswald:wght@400;600&display=swap">
<style>
  :root {
    --purple: #4a1a72;
    --teal: #5bbfca;
    --teal-deep: #52b8c4;
    --ink: #2a2a2a;
    --grey: #a3a3a3;
    --frame: #9a9a9a;
    --paper: #ffffff;
  }
  * { box-sizing: border-box; margin: 0; padding: 0; }
  html, body { width: 1200px; height: 801px; overflow: hidden; background: var(--paper); }
  body { position: relative; font-family: "Alegreya Sans", sans-serif; color: var(--ink); }

  .panel { position: absolute; top: 56px; width: 501px; height: 687px; border: 1px solid var(--frame); overflow: hidden; }
  .panel--back { left: 52px; background: var(--paper); }
  .panel--front { left: 643px; background: linear-gradient(180deg, #ffffff 0%, #f7fbfc 38%, #c9e9ee 55%, #8fd2da 75%, var(--teal-deep) 100%); }

  .brand { position: absolute; display: flex; align-items: center; }
  .brand__ring { border: 3px solid var(--teal); border-radius: 50%; flex: none; }
  .brand__name { font-family: "Fjalla One", sans-serif; color: var(--purple); line-height: 1; white-space: nowrap; }
  .brand__tag { position: absolute; font-family: "Fjalla One", sans-serif; color: var(--purple); white-space: nowrap; letter-spacing: .02em; }

  /* back */
  .back-brand { left: 138px; top: 137px; }
  .back-brand .brand__ring { width: 78px; height: 78px; margin-right: 10px; }
  .back-brand .brand__name { font-size: 27px; }
  .back-tag { left: 226px; top: 205px; font-size: 15px; }

  .info-icon { position: absolute; left: 88px; width: 42px; height: 42px; }
  .copy { position: absolute; left: 138px; width: 270px; font-size: 10.6px; line-height: 13px; }
  .copy p + p { margin-top: 7px; }
  .copy__lead { font-family: "Fjalla One", sans-serif; color: var(--purple); font-size: 14px; }
  .copy strong { font-weight: 700; }

  .ingredients-box { position: absolute; left: 138px; top: 399px; width: 262px; height: 24px; border: 1px solid #555; font-family: "Oswald", sans-serif; font-size: 7.5px; padding: 1px 3px; }
  .storage-box { position: absolute; left: 138px; top: 547px; width: 263px; height: 20px; border: 2px solid var(--teal); font-family: "Oswald", sans-serif; font-size: 7.6px; padding: 3px 4px; white-space: nowrap; }
  .storage-box strong { font-weight: 600; }

  /* front */
  .pet-food-only { position: absolute; top: 17px; width: 100%; text-align: center; font-family: "Fjalla One", sans-serif; font-size: 18px; color: var(--grey); letter-spacing: .02em; }
  .front-brand { left: 63px; top: 112px; }
  .front-brand .brand__ring { width: 114px; height: 114px; margin-right: 10px; }
  .front-brand .brand__name { font-size: 35px; }
  .front-tag { left: 187px; top: 204px; font-size: 21px; }

  .made-badge { position: absolute; left: 336px; top: 235px; width: 84px; height: 84px; }
  .name-sticker { position: absolute; left: 97px; top: 320px; width: 307px; height: 167px; }
  .window-marks { position: absolute; left: 120px; top: 506px; width: 262px; height: 57px; }
  .web-cta { position: absolute; top: 578px; width: 100%; text-align: center; font-family: "Fjalla One", sans-serif; color: var(--purple); font-size: 19.5px; line-height: 18px; }
</style>
</head>
<body>

<section class="panel panel--back" aria-label="Back of pouch">
  <div class="brand back-brand">
    <span class="brand__ring"></span>
    <span class="brand__name">Tailwag Depot</span>
  </div>
  <div class="brand__tag back-tag">100% NATURAL PET TREAT</div>

  <svg class="info-icon" style="top:240px" viewBox="0 0 42 42" aria-hidden="true">
    <circle cx="21" cy="21" r="18" fill="none" stroke="var(--teal)" stroke-width="3"/>
    <path d="M13 21 l6 6 l11 -12" fill="none" stroke="var(--teal)" stroke-width="3.5" stroke-linecap="round" stroke-linejoin="round"/>
  </svg>
  <svg class="info-icon" style="top:334px" viewBox="0 0 42 42" aria-hidden="true">
    <circle cx="21" cy="21" r="18" fill="none" stroke="var(--teal)" stroke-width="3"/>
    <path d="M10 13 h4 l3 11 h12 l2 -8 h-15" fill="var(--teal)" stroke="var(--teal)" stroke-width="2" stroke-linejoin="round"/>
    <circle cx="18" cy="29" r="2" fill="var(--teal)"/><circle cx="28" cy="29" r="2" fill="var(--teal)"/>
  </svg>
  <svg class="info-icon" style="top:500px" viewBox="0 0 42 42" aria-hidden="true">
    <circle cx="21" cy="21" r="18" fill="none" stroke="var(--teal)" stroke-width="3"/>
    <circle cx="21" cy="21" r="10" fill="none" stroke="var(--teal)" stroke-width="2"/>
    <ellipse cx="21" cy="21" rx="4.5" ry="10" fill="none" stroke="var(--teal)" stroke-width="1.6"/>
    <path d="M11 21 h20" stroke="var(--teal)" stroke-width="1.6"/>
  </svg>

  <div class="copy" style="top:237px">
    <p><span class="copy__lead">Tailwag Depot</span> is proudly Australian owned.<br>Our treats are sustainably sourced using human grade ingredients from reputable Australian suppliers.</p>
    <p>Tailwag Depot products can be purchased at any time through our online store.</p>
    <p><span>Our <strong>Tailwag Depot treats</strong> can be purchased through our online store, where you will find a growing range of other brands and products for your dogs, cats, birds, fish, rabbits, guinea pigs, horses, cows, sheep, chickens and more.</span></p>
  </div>

  <div class="ingredients-box">Space for Ingredients:</div>

  <div class="copy" style="top:433px; line-height:12.2px">
    <p>This product is intended as a daily treat and suitable for dogs of all breeds, ages, sizes and activity levels. Always select a treat suitable for your dogs individual needs. Ensure fresh clean drinking water is available at all times and alway supervise your pet when feeding treats.</p>
  </div>

  <div class="copy" style="top:502px">
    <p>For further information,<br>please visit our web site www.tailwagdepot.com.au<br>or contact us at info@tailwagdepot.com.au.</p>
  </div>

  <div class="storage-box"><strong>Storage:</strong> For optimal freshness, seal bag well and store in a cool dry and dark location.</div>
</section>

<section class="panel panel--front" aria-label="Front of pouch">
  <div class="pet-food-only">PET FOOD ONLY</div>
  <div class="brand front-brand">
    <span class="brand__ring"></span>
    <span class="brand__name">Tailwag Depot</span>
  </div>
  <div class="brand__tag front-tag">100% NATURAL PET TREATS</div>

  <svg class="made-badge" viewBox="0 0 84 84" role="img" aria-label="Australian made and owned badge">
    <circle cx="42" cy="42" r="41" fill="#2a2f7a"/>
    <circle cx="42" cy="42" r="34" fill="#ffffff"/>
    <circle cx="42" cy="42" r="22" fill="#2a2f7a"/>
  </svg>

  <svg class="name-sticker" viewBox="0 0 307 167" aria-label="Space for product name sticker">
    <path d="M20 22 Q153 -10 287 22 Q307 28 307 48 L307 128 Q307 142 287 146 Q153 176 20 146 Q0 142 0 128 L0 48 Q0 28 20 22 Z" fill="#ffffff"/>
  </svg>

  <svg class="window-marks" viewBox="0 0 262 57" aria-label="Window area" fill="none" stroke="#ffffff" stroke-width="2">
    <path d="M1 11 V1 H11"/><path d="M251 1 H261 V11"/><path d="M1 46 V56 H11"/><path d="M251 56 H261 V46"/>
  </svg>

  <div class="web-cta">Visit our web site for more pet products<br>www.tailwagdepot.com.au</div>
</section>

</body>
</html>
```